Buch-/eBook-Cover für Traumatherapeutin
Zielgruppe
Ich bin Traumatherapeutin und schreibe ein Buch zum Thema Trauma bearbeiten.
Meine Zielgruppe sucht Heilung, Genesung, Selbstliebe etc.
Aufgabenstellung
Buchcover
Bitte erstell mir ein modernes positives inspirierendes Buchcover mit dem
Titel: 'Morgenlicht NEU entdecken“
Untertitel: „Spüre den Mut der ganz in dir wohnt“
Dr. Mira Kessow
Ich hätte gerne ein modernes Buch, das entweder einen Bezug zum Thema Trauma hat oder aber einfach stylische Schriftzüge. Bin aber auch offen für andere Vorschläge.
Dunkelblau, weiß und türkis oder auch rosa mag ich ganz gerne. Wobei Dunkelblau, weiß und türkis meine Favoriten sind und mit rosa höchstens kleinere Akzente gesetzt werden sollten.
Das Buchcover soll modern sein und direkt ansprechen. Gerne eine originelle Lösung, oder etwas Besonderes, etwas das Tiefe ausdrückt, oder man mehrmals hinsehen muss um etwas zu erkennen oder etwas das mehr Interpretationsspielraum lässt.
Gerne auch viel weiß, zumindest heller und nicht zu dunkel. Stylish, aber nicht überfrachtet.
Schreib mich gerne an, wenn du Fragen hast.
Ich habe mal zwei Beispiel von Typolösungen angehängt, die ich ganz cool fände.
Ich freue mich auf deine Ideen :-)
Ganz liebe Grüße
Mira

```html
<!DOCTYPE html>
<html lang="de">
<head>
<meta charset="utf-8">
<title>Morgenlicht NEU entdecken – Buchcover</title>
<link rel="stylesheet" href="https://fonts.googleapis.com/css2?family=Londrina+Solid:wght@400&family=Montserrat:wght@600;700&display=swap">
<style>
  :root {
    --stage: #8f8f8f;
    --teal: #43bfb8;
    --navy: #22466b;
    --white: #ffffff;
    --pink: #e8237f;
    --sky-light: #a9d8ec;
    --sky-mid: #6fa6dc;
  }
  html, body {
    margin: 0;
    padding: 0;
    width: 668px;
    height: 1200px;
    overflow: hidden;
    background: var(--stage);
  }
  .book-cover {
    position: absolute;
    left: 34px;
    top: 152px;
    width: 600px;
    height: 895px;
    background: var(--teal);
    box-shadow: 4px 6px 14px rgba(0,0,0,0.25);
    overflow: hidden;
  }
  .cover-art {
    position: absolute;
    inset: 0;
    width: 600px;
    height: 895px;
  }
  .author {
    position: absolute;
    top: 54px;
    left: 0;
    width: 600px;
    margin: 0;
    text-align: center;
    font-family: "Montserrat", sans-serif;
    font-weight: 700;
    font-size: 23px;
    letter-spacing: 3px;
    color: var(--white);
  }
  .title-text {
    font-family: "Londrina Solid", sans-serif;
    font-weight: 400;
  }
  .title-line--light { fill: var(--white); }
  .title-line--dark { fill: var(--navy); }
  .subtitle {
    position: absolute;
    left: 238px;
    top: 668px;
    margin: 0;
    font-family: "Montserrat", sans-serif;
    font-weight: 600;
    font-size: 32px;
    line-height: 41px;
    color: var(--navy);
  }
  .subtitle span { display: block; white-space: nowrap; }
</style>
</head>
<body>
  <main class="book-cover">
    <svg class="cover-art" viewBox="0 0 600 895" xmlns="http://www.w3.org/2000/svg">
      <defs>
        <linearGradient id="planeTone" x1="0" y1="0" x2="1" y2="1">
          <stop offset="0" stop-color="var(--sky-light)"/>
          <stop offset="1" stop-color="var(--sky-mid)"/>
        </linearGradient>
      </defs>

      <path class="wave-band" fill="var(--navy)"
            d="M0 680 C 180 610, 420 575, 600 602 L 600 895 L 0 895 Z"/>
      <path class="lower-field" fill="var(--white)"
            d="M0 716 C 180 645, 430 610, 600 658 L 600 895 L 0 895 Z"/>

      <text class="title-text title-line--light" x="50" y="205" font-size="125"
            textLength="496" lengthAdjust="spacingAndGlyphs">MORGENLICHT</text>
      <text class="title-text title-line--dark" x="50" y="412" font-size="262"
            textLength="496" lengthAdjust="spacingAndGlyphs">NEU</text>
      <text class="title-text title-line--light" x="50" y="530" font-size="128"
            textLength="496" lengthAdjust="spacingAndGlyphs">ENTDECKEN</text>

      <rect class="plane-illustration" role="img"
            aria-label="Aquarell-Papierflieger in Hellblau mit gestrichelter Flugbahn in Pink"
            x="40" y="584" width="186" height="130" rx="12" fill="url(#planeTone)"/>

      <path class="accent-underline" fill="none" stroke="var(--pink)" stroke-width="7"
            stroke-linecap="round" d="M256 836 C 340 826, 450 820, 548 821"/>
    </svg>

    <p class="author">DR. MIRA KESSOW</p>

    <p class="subtitle">
      <span>Spüre den Mut</span>
      <span>der ganz</span>
      <span>in dir wohnt</span>
    </p>
  </main>
</body>
</html>
```